home accents e-commerce website

I'd like a professional simple website designed where I can sell my home goods. I already have my domain name registered. I need the website to accept credit card payments and Monvex. It should have a shopping cart option and calculate sales tax and shipping costs on merchandise automatically.

I'll be taking photographs of the merchandise and writing product descriptions myself. (I'm not a professional photographer, so these photos probably won't look too polished. If you can help me make them look better, that'd be great). As I add new merchandise in the future, I'd like an option where I can log in to the back end myself and add pictures/product descriptions. And take old products down as they sell out. So the website needs to be user-friendly for me, even though I'm completely web design illiterate!

I'd like a creative, talented person who can create a whimsical, cute website. Nothing too corporate-looking.

Thank you!

Target Market(s)

women, online shoppers, New York City-area, (ship products to the United States only)

Industry/Entity Type

Home And Garden

Coding

Coded - Design and coding required

Number of Pages Required

1 page

Font styles to use
Sans Serif

Colors
0355a3
ffffff

Requirements
Must have
• shopping cart feature
• safe, secure credit card and Monvex payments
• ability for me to go in and add new products and take down old/sold products
Nice to have
• whimsical, cute design
Should not have
• too corporate-looking

```html
<!DOCTYPE html>
<html lang="en">
<head>
<meta charset="utf-8">
<title>Wrenly Home Goods</title>
<link href="https://fonts.googleapis.com/css2?family=Roboto:wght@300;400;500;700&display=swap" rel="stylesheet">
<style>
:root{
  --brand:#0355a3;
  --brand-dark:#0a3f7e;
  --white:#ffffff;
  --ink:#333333;
  --muted:#777777;
  --line:#e2e2e2;
  --panel:#f1f1f1;
  --footer:#2f2f2f;
  --footer-line:#444444;
  --footer-text:#cccccc;
}
*{box-sizing:border-box;margin:0;padding:0}
html,body{width:744px;height:1200px;overflow:hidden;background:var(--white)}
body{position:relative;font-family:'Roboto',Arial,sans-serif;color:var(--ink)}
.abs{position:absolute}

/* header */
.logo{left:82px;top:18px}
.logo-name{font-size:40px;font-weight:700;color:var(--brand);letter-spacing:1px;line-height:42px}
.logo-tag{font-size:12px;font-weight:400;color:var(--brand);letter-spacing:6.5px;margin-top:2px}
.social{top:36px;left:498px;display:flex;gap:6px}
.social span{width:20px;height:20px;border-radius:50%;border:1px solid var(--brand);display:block}
.social span.alt{border-color:#c9302c}
.cart{left:612px;top:37px;text-align:right;font-size:7px;color:var(--brand);line-height:9px}
.cart b{display:block;font-size:8px;font-weight:400}
.cart-btn{left:642px;top:36px;width:20px;height:20px;border-radius:50%;background:var(--brand)}

/* nav */
.nav{top:88px;left:0;width:744px;height:25px;background:var(--brand)}
.nav a{position:absolute;top:0;height:25px;line-height:25px;color:var(--white);font-size:8px;font-weight:500;text-decoration:none;text-align:center}
.nav .active{left:82px;width:153px;background:var(--brand-dark)}

/* hero */
.hero{top:113px;left:0;width:744px;height:268px;background:linear-gradient(90deg,#4a4a40 0%,#8a8a78 22%,#cfcdbf 45%,#e9e7dc 70%,#d8d6cc 100%)}
.hero-arrow{top:240px;width:17px;height:17px;border-radius:50%;background:#555;display:flex;align-items:center;justify-content:center}
.hero-box{left:414px;top:182px;width:248px;height:129px;background:rgba(255,255,255,.92);padding:16px 15px;text-align:right}
.hero-box h1{font-size:15px;font-weight:400;line-height:18px;letter-spacing:.3px;color:#222}
.hero-box p{font-size:6.5px;color:var(--muted);line-height:10px;margin-top:5px;padding-left:10px}
.btn-outline{display:inline-block;margin-top:10px;border:1px solid #444;font-size:9px;padding:7px 8px;color:#222}

/* sidebar */
.cat-head{left:82px;top:420px;width:148px;height:30px;background:var(--brand);color:var(--white);font-size:10px;font-weight:500;line-height:30px;padding-left:10px}
.cats{left:82px;top:450px;width:148px;list-style:none;background:var(--panel)}
.cats li{height:30px;line-height:30px;border-bottom:1px solid var(--line);font-size:8px;color:#555;padding-left:20px;position:relative}
.cats li::before{content:"";position:absolute;left:11px;top:12px;border-left:3px solid #888;border-top:3px solid transparent;border-bottom:3px solid transparent}
.cats li.on{color:var(--brand)}
.cats li.on::before{border-left-color:var(--brand)}
.promo{left:82px;top:733px;width:148px;height:173px;background:linear-gradient(160deg,#9fb8d0 0%,#c9b79a 55%,#a5582a 100%)}
.promo-btn{left:124px;top:809px;width:64px;height:22px;background:var(--white);font-size:9px;text-align:center;line-height:22px;color:#222}

/* products */
.prod-head{left:255px;top:429px;font-size:10px;font-weight:500;color:#222}
.pager-mini{top:428px;width:14px;height:13px;border:1px solid #bbb;display:flex;align-items:center;justify-content:center}
.card{width:129px}
.card .img{height:119px}
.card .name{font-size:7.5px;color:var(--muted);margin-top:9px}
.card .price{font-size:7.5px;color:var(--muted);margin-top:4px}
.pages{left:255px;top:954px;display:flex;gap:3px}
.pages span{width:18px;height:18px;background:#e6e6e6;font-size:7px;color:#555;text-align:center;line-height:18px}
.pages span.cur{background:#555;color:var(--white)}
.pages span.gap{margin-left:4px}

/* footer */
.footer{top:1022px;left:0;width:744px;height:178px;background:var(--footer)}
.f-head{top:1059px;font-size:9px;color:var(--white);font-weight:400}
.email{left:82px;top:1078px;width:137px;height:25px;background:var(--white);font-size:6px;color:#333;line-height:25px;padding-left:10px}
.links{top:1076px;list-style:none;font-size:6px;color:var(--footer-text);line-height:12.8px}
.f-social{left:446px;top:1078px;display:flex;gap:4px}
.f-social span{width:16px;height:16px;border-radius:50%;background:#666;display:block}
.pay{left:565px;top:1078px;display:flex;gap:5px}
.pay span{height:11px;padding:0 3px;background:var(--white);font-size:4.5px;font-weight:700;color:#333;line-height:11px}
.f-rule{left:0;top:1158px;width:744px;height:1px;background:var(--footer-line)}
.copy{left:0;top:1175px;width:744px;text-align:center;font-size:6px;color:var(--footer-text)}
</style>
</head>
<body>

<div class="abs logo">
  <div class="logo-name">wrenly</div>
  <div class="logo-tag">HOME GOODS</div>
</div>
<div class="abs social"><span></span><span></span><span></span><span class="alt"></span></div>
<div class="abs cart">My Cart<b>$00.00</b></div>
<div class="abs cart-btn">
  <svg width="20" height="20" viewBox="0 0 20 20"><path d="M6 7h1.2l1 4.5h4.3l.9-3.2H8" fill="none" stroke="#fff" stroke-width="1"/><circle cx="8.7" cy="13" r=".8" fill="#fff"/><circle cx="12.2" cy="13" r=".8" fill="#fff"/></svg>
</div>

<nav class="abs nav">
  <a class="active" href="#">ABOUT WRENLY</a>
  <a href="#" style="left:290px;width:180px">HOW DOES THIS CRAZINESS WORK?</a>
  <a href="#" style="left:570px;width:62px">CONTACT</a>
</nav>

<section class="abs hero" role="img" aria-label="Bedroom with bedside lamp, textured wall and white bedding"></section>
<div class="abs hero-arrow" style="left:16px"><svg width="8" height="8" viewBox="0 0 8 8"><path d="M5 1 2 4l3 3" fill="none" stroke="#fff" stroke-width="1.4"/></svg></div>
<div class="abs hero-arrow" style="left:711px"><svg width="8" height="8" viewBox="0 0 8 8"><path d="M3 1l3 3-3 3" fill="none" stroke="#fff" stroke-width="1.4"/></svg></div>
<div class="abs hero-box">
  <h1>ETIAM MASSA<br>ELEMENTUM BIBENDUM</h1>
  <p>Phasellus consequat sagittis nisi suscipit feugiat. Cras eget leo sed nunc hendrerit ultricies eu at nisl.</p>
  <span class="btn-outline">SHOP NOW</span>
</div>

<div class="abs cat-head">PRODUCT CATEGORIES</div>
<ul class="abs cats">
  <li class="on">Vases</li>
  <li>Throw Pillows</li>
  <li>Blankets and Throws</li>
  <li>For Your Floors</li>
  <li>For Your Walls</li>
  <li>For Your Table</li>
  <li>For Your Bedside</li>
  <li>Let THere Be Light</li>
  <li>Put Your Feet Up</li>
</ul>
<div class="abs promo" role="img" aria-label="Room corner with lamp, cushions, picture frames and a wooden cabinet"></div>
<div class="abs promo-btn">SHOP NOW</div>

<div class="abs prod-head">OUR PRODUCTS</div>
<div class="abs pager-mini" style="left:628px"><svg width="6" height="6" viewBox="0 0 6 6"><path d="M4 1 2 3l2 2" fill="none" stroke="#888"/></svg></div>
<div class="abs pager-mini" style="left:646px"><svg width="6" height="6" viewBox="0 0 6 6"><path d="M2 1l2 2-2 2" fill="none" stroke="#888"/></svg></div>

<div class="abs card" style="left:255px;top:450px"><div class="img" role="img" aria-label="Pink peonies in a teal vase" style="background:linear-gradient(180deg,#e7cdbb,#b8a79a)"></div><div class="name">Maecenas tortor accumsan</div><div class="price">$00.00</div></div>
<div class="abs card" style="left:394px;top:450px"><div class="img" role="img" aria-label="Blue glass bottle with purple flowers by a window" style="background:linear-gradient(180deg,#cfd6dc,#9aa6b2)"></div><div class="name">Maecenas tortor accumsan</div><div class="price">$00.00</div></div>
<div class="abs card" style="left:533px;top:450px"><div class="img" role="img" aria-label="Orange flowers in a white vase on red background" style="background:linear-gradient(180deg,#e8707a,#d94c55)"></div><div class="name">Maecenas tortor accumsan</div><div class="price">$00.00</div></div>

<div class="abs card" style="left:255px;top:618px"><div class="img" role="img" aria-label="Pink lilies in a white jug on blue background" style="background:linear-gradient(180deg,#a9d4e4,#cfe6ee)"></div><div class="name">Maecenas tortor accumsan</div><div class="price">$00.00</div></div>
<div class="abs card" style="left:394px;top:618px"><div class="img" role="img" aria-label="Blossom branch in a white vase" style="background:linear-gradient(180deg,#f3efec,#e2dcd8)"></div><div class="name">Maecenas tortor accumsan</div><div class="price">$00.00</div></div>
<div class="abs card" style="left:533px;top:618px"><div class="img" role="img" aria-label="Carved golden vase on dark background" style="background:linear-gradient(180deg,#5a4d4a,#2e2826)"></div><div class="name">Maecenas tortor accumsan</div><div class="price">$00.00</div></div>

<div class="abs card" style="left:255px;top:787px"><div class="img" role="img" aria-label="Succulent in a white geometric pot" style="background:linear-gradient(180deg,#b5b5b3,#e4e4e2)"></div><div class="name">Maecenas tortor accumsan</div><div class="price">$00.00</div></div>
<div class="abs card" style="left:394px;top:787px"><div class="img" role="img" aria-label="Pale roses in a white pitcher" style="background:linear-gradient(180deg,#ecebe7,#d7d3cc)"></div><div class="name">Maecenas tortor accumsan</div><div class="price">$00.00</div></div>
<div class="abs card" style="left:533px;top:787px"><div class="img" role="img" aria-label="Pink roses bouquet in a white tin vase" style="background:linear-gradient(180deg,#e8e6e4,#d5cfcc)"></div><div class="name">Maecenas tortor accumsan</div><div class="price">$00.00</div></div>

<div class="abs pages">
  <span class="cur">1</span><span>2</span><span>3</span><span>4</span><span>5</span>
  <span class="gap">&lsaquo;</span><span>&rsaquo;</span>
</div>

<footer class="abs footer"></footer>
<div class="abs f-head" style="left:82px">STAY CONNECTED</div>
<div class="abs email">Email Address
  <svg class="abs" style="left:117px;top:8px" width="10" height="8" viewBox="0 0 10 8"><rect width="10" height="8" fill="#333"/><path d="M0 0l5 4 5-4" fill="none" stroke="#fff" stroke-width=".8"/></svg>
</div>
<div class="abs f-head" style="left:256px">LINKS</div>
<ul class="abs links" style="left:256px">
  <li>• Home</li><li>• About</li><li>• Wrenly How does this craziness work?</li><li>• Contact</li>
</ul>
<ul class="abs links" style="left:380px">
  <li>• My Cart</li><li>• My Account</li><li>• My Wishlist</li><li>• Checkout</li>
</ul>
<div class="abs f-head" style="left:446px">FOLLOW US ON</div>
<div class="abs f-social"><span></span><span></span><span></span><span></span></div>
<div class="abs f-head" style="left:565px">PAYMENTS</div>
<div class="abs pay"><span>Monvex</span><span>Carda</span><span>Norvia Lite</span><span>Norvia</span></div>
<div class="abs f-rule"></div>
<div class="abs copy">Copyright © 2017 Wrenly.&nbsp;&nbsp; All rights reserved.</div>

</body>
</html>
```